Yoga Workshop - Yoga Practice information flyer

I am a yoga teacher who will be presenting a workshop on yoga for sleep and need a brochure for my clients which outlines a practice that I give them so they can do the practice at home. Ideally I would like a brochure that is a single A3 size of paper in size that folds in half to an A4 booklet with the entire practice on the centre section to make it easy for people to do the practice at home with just one open page in front of them:
* Front page detailing "Yoga for Sleep Workshop" and "Restorative Yoga Practice"
* Centre contains the information on the practice contained in the attached word document. The practice consists of 5 postures, so there needs to be five separate sections which have the pictures of the postures (attached in uploaded files) and the wording contained in the attached word document. All pictures uploaded need to be included in the flyer as each posture has different pictures demonstrating the posture using yoga props or using things people have at home
* Back page containing a picture of myself (picture uploaded in files) with some information about me (contained in the attached word document) and my website www.calmdrift.com.au

I also need this flyer to be able to printed on 2 double sided A4 sheets of paper so will require 2 x pdf file versions. Importantly, for the centre section of the flyer, the design needs to ensure if it is printed on A4 paper, the wording and pictures for each of the postures are not separated over two pages

Target Market(s)

Existing clients

Requirements
Must have
• Detailed in project description
Nice to have
• The word document also contains some quotes. These do not need to be included in the flyer. If there is room and there is room for one or two of those please include where it would look good
Should not have
• Stock pictures of people in yoga postures which a normal everyday person could not get into

```html
<!DOCTYPE html>
<html lang="en">
<head>
<meta charset="utf-8">
<title>Restorative Yoga Practice – Postures 1 &amp; 2</title>
<link href="https://fonts.googleapis.com/css2?family=Josefin+Sans:ital,wght@0,400;0,700;1,400&display=swap" rel="stylesheet">
<style>
  :root {
    --rust: #a63a24;
    --gold: #f5c32c;
    --cream: #fbf3ea;
    --frame: #ffffff;
    --photo-light: #b9a79a;
    --photo-dark: #6e3c22;
  }
  * { box-sizing: border-box; margin: 0; padding: 0; }
  html, body { width: 848px; height: 1200px; overflow: hidden; }
  body {
    background: var(--rust);
    font-family: "Josefin Sans", sans-serif;
    color: var(--cream);
    position: relative;
  }
  .photo {
    position: absolute;
    width: 231px;
    height: 357px;
    background: var(--frame);
    padding: 5px;
  }
  .photo-fill {
    width: 100%;
    height: 100%;
    background: linear-gradient(180deg, var(--photo-light) 0%, var(--photo-dark) 100%);
  }
  .posture {
    position: absolute;
    left: 35px;
    width: 766px;
  }
  .posture-title {
    font-weight: 700;
    font-size: 19.5px;
    line-height: 24px;
    color: var(--gold);
    letter-spacing: .4px;
    margin-bottom: 13px;
  }
  .posture p {
    font-size: 14.8px;
    line-height: 15.7px;
    letter-spacing: .5px;
    margin-bottom: 15.7px;
    hyphens: manual;
  }
  .label {
    font-style: italic;
    color: var(--gold);
  }
</style>
</head>
<body>

  <div class="photo" style="left:35px; top:29px;"><div class="photo-fill" role="img" aria-label="Photo: woman lying on a yoga mat with a bolster under her knees and along her spine"></div></div>
  <div class="photo" style="left:302px; top:29px;"><div class="photo-fill" role="img" aria-label="Photo: woman lying on a yoga mat with rolled towels under her knees and spine"></div></div>
  <div class="photo" style="left:570px; top:29px;"><div class="photo-fill" role="img" aria-label="Photo: woman sitting at the base of a rolled towel, preparing to lie back"></div></div>

  <section class="posture" style="top:408px;">
    <h2 class="posture-title">Posture 1 - Supported Chest Opening with Knee Support</h2>
    <p><span class="label">Props</span> - 2 x bolsters (or towels rolled up lengthways), 1 x cushion for head support (optional)</p>
    <p><span class="label">Set up notes</span> - Position the props in a T-position with one bolster/towel running parallel to the yoga mat and one bolster towel running horizontal to the mat underneath the knees. Position yourself so your buttocks is on the floor and the parallel bolster runs from the lower back up to behind the head.</p>
    <p><span class="label">Caution</span> - If any lower back pain is experience adjust the parallel bolster height by using a towel. If using a towel, the height of the parallel support prop can be adjusted by either using a thinner towel or loosely roll&shy;ing the towel. Do not us any parallel support prop if pain continues.</p>
  </section>

  <div class="photo" style="left:171px; top:613px;"><div class="photo-fill" role="img" aria-label="Photo: woman in reclined bound-angle pose with knees supported by yoga blocks"></div></div>
  <div class="photo" style="left:439px; top:613px;"><div class="photo-fill" role="img" aria-label="Photo: woman in reclined bound-angle pose with knees supported by pillows"></div></div>

  <section class="posture" style="top:992px;">
    <h2 class="posture-title">Posture 2 - Supported Bound-Angle Pose</h2>
    <p><span class="label">Props</span> - 1 x bolsters (or towel rolled up lengthways), 2 x yoga blocks/bolsters (or pillows), 1 x cushion for head support (optional)</p>
    <p><span class="label">Set up notes</span> - Similar to Posture 1 without the bolster behind the knees. Instead, the soles of the feet are together with knees wide being supported by either blocks, bolsters or pillows.</p>
    <p><span class="label">Caution</span> - If any lower back pain is experience adjust the parallel bolster height by using a towel. If using a towel, the height of the parallel support prop can be adjusted by either using a thinner towel or loosely roll&shy;ing the towel. Do not us any parallel support prop if pain continues.</p>
  </section>

</body>
</html>
```